Marlowby Services Website Design

We have most content but require a professional design. We have a logo already and will need it utilized along with several of the photos from the attached documentation.
First page should have our mission and Vision and the synapsis provided in the word document. Visitors will be prompted to select from one of our 3 divisions from this page.
Each division will have the same list of tabs : About, Services, Safety, Careers and Contact.
Photos on each divisions page should be representative of the divisions offerings. The word doc attached contains the requested content and we are open to edits that would complement and fill the website.
I like the Quorvane site www.quorvane.example - they are our competition so cant be modeled directly after this.
Please include prompts to request quote at each service page. align the format of the geotechnical page to the other 2 divisions.
I used chat gpt for some of the content so will need it optimized for SCO.

```html
<!DOCTYPE html>
<html lang="en">
<head>
<meta charset="utf-8">
<title>Marlowby Services</title>
<link rel="stylesheet" href="https://fonts.googleapis.com/css2?family=Poppins:wght@400;600;700;800&family=Rubik:wght@400;500&family=Figtree:wght@400;500;600&family=Roboto:wght@400;500&display=swap">
<style>
:root{
  --red:#e8202a;
  --pink:#f4aeb0;
  --ink:#1d1d1f;
  --body:#2a2a2a;
  --grey:#8a8a8a;
  --page:#f8f8f8;
  --white:#ffffff;
}
*{margin:0;padding:0;box-sizing:border-box}
html,body{width:1200px;height:2407px;overflow:hidden;background:var(--page)}
body{position:relative;font-family:"Figtree",sans-serif;color:var(--body)}
.abs{position:absolute}

/* hero */
.hero{left:0;top:0;width:1200px;height:634px;background:linear-gradient(180deg,#2f3e4c 0%,#3a4652 45%,#333a3e 75%,#2a2c2c 100%)}
.hero-photo{position:absolute;inset:0;background:linear-gradient(90deg,rgba(20,28,36,.35),rgba(60,66,72,.2) 60%,rgba(20,24,28,.35))}
.wordmark{font-family:"Poppins",sans-serif;font-weight:800;color:var(--red);letter-spacing:6px;line-height:1}
.hero .wordmark{left:56px;top:216px;font-size:62px}
.tagline{left:56px;top:288px;width:520px;font-family:"Poppins",sans-serif;font-weight:700;font-size:28px;line-height:41.5px;color:var(--white)}
.hero-choose{left:700px;top:262px;width:370px;text-align:center;font-family:"Poppins",sans-serif;font-weight:700;font-size:37px;color:var(--red)}
.division-btn{top:333px;width:156px;height:43px;border:1.5px solid var(--white);border-radius:3px;color:var(--white);font-family:"Figtree",sans-serif;font-size:14px;display:flex;align-items:center;justify-content:center}

/* section titles */
.section-title{left:0;width:1200px;text-align:center;font-family:"Rubik",sans-serif;font-weight:500;font-size:28px;color:var(--ink)}
.title-rule{left:551px;width:97px;height:5px;border-radius:3px;background:var(--red)}

/* about */
.about-art{left:28px;top:795px;width:533px;height:374px;border-radius:8px;background:radial-gradient(ellipse at 55% 60%,#e8363c 0%,#f08a8d 40%,#f3e6e6 75%,var(--page) 100%)}
.about-copy{left:585px;top:810px;width:545px}
.about-copy h3{font-family:"Poppins",sans-serif;font-weight:700;font-size:22px;color:var(--red);line-height:1.2}
.about-copy p{font-size:15px;line-height:21px;color:var(--ink)}
.about-copy .hl{color:var(--red)}
.mission{margin-top:18px}
.btn-red{left:585px;top:1113px;width:118px;height:44px;background:var(--red);color:var(--white);border-radius:3px;font-family:"Poppins",sans-serif;font-weight:600;font-size:11.5px;display:flex;align-items:center;justify-content:center}

/* divisions */
.blob{border-radius:50%;background:var(--pink)}
.division-card{top:1332px;width:270px;height:259px;background:var(--white);border-radius:8px;text-align:center;box-shadow:0 2px 10px rgba(0,0,0,.04)}
.division-icon{margin:21px auto 0;width:62px;height:62px;border:1.5px solid var(--red);border-radius:8px;display:flex;align-items:center;justify-content:center}
.division-card h4{margin-top:14px;font-family:"Rubik",sans-serif;font-weight:500;font-size:20px;color:var(--red)}
.division-card p{margin:14px auto 0;width:220px;font-size:14px;line-height:19px;color:#444}

/* testimonials */
.review{top:1758px;width:257px;height:168px;background:var(--white);padding:14px 9px 0}
.review .quote{font-size:10.5px;line-height:15px;color:var(--grey);height:62px}
.review .more{margin-top:4px;font-size:10.5px;font-weight:600;color:var(--red);height:15px}
.review .name{position:absolute;left:9px;top:110px;font-family:"Rubik",sans-serif;font-weight:500;font-size:16px;color:var(--ink)}
.review .stars{position:absolute;left:9px;top:138px;display:flex;gap:4px}
.review .when{position:absolute;right:9px;top:140px;font-size:10.5px;color:var(--grey)}
.pager-btn{top:1960px;width:43px;height:43px;border:1.2px solid var(--ink);border-radius:50%;display:flex;align-items:center;justify-content:center}
.dots{left:561px;top:1978px;display:flex;gap:6px;align-items:center}
.dot{width:6px;height:6px;border-radius:50%;background:#9a9a9a}
.dot.on{width:28px;border-radius:3px;background:var(--red)}

/* footer */
.footer{left:0;top:2087px;width:1200px;height:320px;background:var(--white)}
.footer .wordmark{left:148px;top:55px;font-size:31px;letter-spacing:3px}
.footer-blurb{left:148px;top:100px;width:205px;font-size:10.5px;line-height:15px;color:var(--ink)}
.footer-col{top:50px}
.footer-col h5{font-family:"Roboto",sans-serif;font-weight:500;font-size:16px;color:var(--ink);margin-bottom:6px}
.footer-col li{list-style:none;font-family:"Roboto",sans-serif;font-size:10.5px;line-height:21.5px;color:var(--ink)}
.social{top:2215px;width:22px;height:22px;border-radius:50%;background:#c9c9c9}
.footer-rule{left:116px;top:2345px;width:966px;height:1px;background:#7a7a7a}
.copyright{left:0;top:2368px;width:1200px;text-align:center;font-size:11px;color:var(--grey)}
</style>
</head>
<body>

<section class="abs hero">
  <div class="hero-photo" role="img" aria-label="Industrial power plant with tall red and white striped smokestacks under a dusky sky"></div>
  <div class="abs wordmark">MARLOWBY</div>
  <h1 class="abs tagline">Providing Safe, Reliable Air Access And Maintenance Services For Your Own Business.</h1>
  <h2 class="abs hero-choose">Choose Division</h2>
  <div class="abs division-btn" style="left:625px">Air Access</div>
  <div class="abs division-btn" style="left:807px">Geotechnical Drilling</div>
  <div class="abs division-btn" style="left:989px">Renewable Energy</div>
</section>

<h2 class="abs section-title" style="top:718px">About Us</h2>
<div class="abs title-rule" style="top:758px"></div>

<div class="abs about-art" role="img" aria-label="Illustration of a red factory with cooling towers, storage tanks and a delivery truck"></div>

<div class="abs about-copy">
  <h3>Our Vision:</h3>
  <p>To be a leading provider of <span class="hl">air access</span>, <span class="hl">geotechnical drilling</span> and <span class="hl">service solutions</span>, setting the standard for excellence in safety, efficiency and environmental management.</p>
  <h3 class="mission">Our Mission:</h3>
  <p>Provides unmatched air access, geotechnical drilling, and service and maintenance solutions, consistently exceeding our clients' expectations. We strive to achieve this by investing in cutting-edge technology, cultivating a culture of safety and continuous improvement, and prioritizing environmental sustainability. Through collaboration, integrity and dedication, we aim to contribute to our clients' success while maintaining the highest standards of quality and professionalism.</p>
</div>
<div class="abs btn-red">Learn More</div>

<div class="abs blob" style="left:961px;top:1166px;width:564px;height:564px"></div>
<div class="abs blob" style="left:-245px;top:1263px;width:396px;height:396px"></div>

<h2 class="abs section-title" style="top:1252px">Choose The Division</h2>
<div class="abs title-rule" style="top:1292px"></div>

<div class="abs division-card" style="left:138px">
  <div class="division-icon">
    <svg width="44" height="44" viewBox="0 0 44 44" fill="none" stroke="#e8202a" stroke-width="1.6" stroke-linecap="round"><path d="M6 34c8 6 22 6 30-2"/><path d="M10 28c6 4 16 4 22-2 3-3 2-8-2-8-5 0-6 6-12 6"/><path d="M14 22c-3-5 0-10 3-14M20 20c-2-5 1-9 3-13M26 18c-2-4 0-7 2-10"/></svg>
  </div>
  <h4>Air Access</h4>
  <p>Lorem ipsum dolor sit amet consectetur. Tincidunt consequat sem lectus ornare massa pulvinar nec. Fringilla in malesuada feugiat.</p>
</div>
<div class="abs division-card" style="left:465px">
  <div class="division-icon">
    <svg width="44" height="44" viewBox="0 0 44 44" fill="none" stroke="#e8202a" stroke-width="1.6" stroke-linejoin="round"><rect x="6" y="30" width="32" height="7" rx="3.5"/><circle cx="11" cy="33.5" r="1.5"/><circle cx="17" cy="33.5" r="1.5"/><circle cx="23" cy="33.5" r="1.5"/><circle cx="29" cy="33.5" r="1.5"/><path d="M20 30V20h10l4 6v4"/><path d="M24 20v6h8"/><path d="M20 24 10 14l-4 6"/></svg>
  </div>
  <h4>Geotechnical Drilling</h4>
  <p>Lorem ipsum dolor sit amet consectetur. Et blandit massa cras sed. Est augue libero egestas tempor arcu amet sapien sociis.</p>
</div>
<div class="abs division-card" style="left:791px">
  <div class="division-icon">
    <svg width="44" height="44" viewBox="0 0 44 44" fill="none" stroke="#e8202a" stroke-width="1.6" stroke-linejoin="round"><rect x="7" y="20" width="12" height="16"/><path d="M7 25h12M7 30h12M13 20v16"/><path d="M13 8v4M6 12l3 2M20 12l-3 2"/><circle cx="13" cy="16" r="3"/><path d="M22 28l8-8 8 8v8H22z"/><path d="M28 36v-5h4v5"/></svg>
  </div>
  <h4>Renewable Energy</h4>
  <p>Lorem ipsum dolor sit amet consectetur. Nisl cursus nibh eget donec interdum nulla amet nulla. Vitae cras sed ullamcorper non weqrt.</p>
</div>

<h2 class="abs section-title" style="top:1677px">Testimonial from Our Clients</h2>
<div class="abs title-rule" style="top:1717px"></div>

<svg width="0" height="0" style="position:absolute"><defs><symbol id="star" viewBox="0 0 24 24"><path fill="#e8202a" d="M12 2l2.9 6.6 7.1.6-5.4 4.7 1.6 7-6.2-3.7-6.2 3.7 1.6-7L2 9.2l7.1-.6z"/></symbol></defs></svg>

<div class="abs review" style="left:48px">
  <p class="quote">Lorem ipsum dolor sit amet consectetur. Cursus morbi nisi felis imperdiet diam risus gravida. Imperdiet ac lorem et massa amet malesuada sapien varius non. Tortor arcu in purus blandit.</p>
  <p class="more">Read More</p>
  <div class="name">Tamsin</div>
  <div class="stars"><svg width="15" height="15"><use href="#star"/></svg><svg width="15" height="15"><use href="#star"/></svg><svg width="15" height="15"><use href="#star"/></svg><svg width="15" height="15"><use href="#star"/></svg><svg width="15" height="15"><use href="#star"/></svg></div>
  <div class="when">4 days ago</div>
</div>
<div class="abs review" style="left:324px">
  <p class="quote">Lorem ipsum dolor sit amet consectetur. Lectus facilisi consequat pellentesque amet volutpat est massa velit. Quisque in senectus massa vitae habitasse. Egestas condimentum quisque.</p>
  <p class="more"></p>
  <div class="name">Orrin Vale</div>
  <div class="stars"><svg width="15" height="15"><use href="#star"/></svg><svg width="15" height="15"><use href="#star"/></svg><svg width="15" height="15"><use href="#star"/></svg><svg width="15" height="15"><use href="#star"/></svg><svg width="15" height="15"><use href="#star"/></svg></div>
  <div class="when">4 days ago</div>
</div>
<div class="abs review" style="left:601px">
  <p class="quote">Lorem ipsum dolor sit amet consectetur. Et ultrices vehicula turpis porta dictum. Ac mollis diam auctor diam egestas sit. Sollicitudin lorem consectetur massa eget at tincidunt non. Nisl.</p>
  <p class="more">Read More</p>
  <div class="name">Milo Fenwright</div>
  <div class="stars"><svg width="15" height="15"><use href="#star"/></svg><svg width="15" height="15"><use href="#star"/></svg><svg width="15" height="15"><use href="#star"/></svg><svg width="15" height="15"><use href="#star"/></svg><svg width="15" height="15"><use href="#star"/></svg></div>
  <div class="when">6 days ago</div>
</div>
<div class="abs review" style="left:877px">
  <p class="quote">Lorem ipsum dolor sit amet consectetur. Sem condimentum non eu amet ullamcorper pellentesque auctor. Tincidunt odio at eu.</p>
  <p class="more"></p>
  <div class="name">Ned Carrow</div>
  <div class="stars"><svg width="15" height="15"><use href="#star"/></svg><svg width="15" height="15"><use href="#star"/></svg><svg width="15" height="15"><use href="#star"/></svg><svg width="15" height="15"><use href="#star"/></svg><svg width="15" height="15"><use href="#star"/></svg></div>
  <div class="when">6 days ago</div>
</div>
<div class="abs review" style="left:1153px">
  <p class="quote">Lorem ipsum dolor sit amet consectetur. Pretium egestas.</p>
  <p class="more"></p>
  <div class="name">Ivo</div>
  <div class="stars"><svg width="15" height="15"><use href="#star"/></svg><svg width="15" height="15"><use href="#star"/></svg></div>
</div>

<div class="abs pager-btn" style="left:502px"><svg width="24" height="12" viewBox="0 0 24 12" fill="none" stroke="#1d1d1f" stroke-width="1.6"><path d="M23 6H2M7 1 2 6l5 5"/></svg></div>
<div class="abs dots"><span class="dot on"></span><span class="dot"></span><span class="dot"></span><span class="dot"></span><span class="dot"></span></div>
<div class="abs pager-btn" style="left:654px"><svg width="24" height="12" viewBox="0 0 24 12" fill="none" stroke="#1d1d1f" stroke-width="1.6"><path d="M1 6h21M17 1l5 5-5 5"/></svg></div>

<footer class="abs footer">
  <div class="abs wordmark">MARLOWBY</div>
  <p class="abs footer-blurb">Lorem ipsum dolor sit amet consectetur. Aliquam consequat eget rhoncus suscipit tincidunt enim morbi tristique porta. In amet nisl augue eu. Ullamcorper ipsum lectus sit dolor ut enim nisi mi. Duis.</p>
  <div class="abs footer-col" style="left:444px"><h5>Company</h5><ul><li>About Us</li><li>Our Services</li><li>Sector Business</li><li>Customer Reviews</li><li>Contact Us</li></ul></div>
  <div class="abs footer-col" style="left:639px"><h5>Services</h5><ul><li>Air Access</li><li>Geotechnical Drilling</li><li>Renewable Energy</li><li>Services Solving</li></ul></div>
  <div class="abs footer-col" style="left:842px"><h5>Contact Info</h5><ul><li style="line-height:24px">58 Ridgefield Road Alder Falls AB T0X-1B0</li><li style="line-height:24px">info@marlowbyservices.example</li><li style="line-height:24px">555.014.2290</li></ul></div>
</footer>
<div class="abs social" style="left:933px" aria-label="Social link"></div>
<div class="abs social" style="left:974px" aria-label="Social link"></div>
<div class="abs social" style="left:1015px" aria-label="Social link"></div>
<div class="abs social" style="left:1057px" aria-label="Social link"></div>
<div class="abs footer-rule"></div>
<p class="abs copyright">© 2024 Marlowby. All Rights Reserved.</p>

</body>
</html>
```